Healthy lifestyle Influencer business card

I need your creativity to have a business card that I can leave in all the restaurants, hotels and spas I visit to inform them that I am an influencer specializing in the wellness sector and that I will write a review about them. You can use my instagram photos Lunavita27 or on my website www.piattileggeriorto.it. I would like my business card to impress with its creativity! thank you very much!

Contact Information for Business Card

siteweb, instagram, phone number

Font styles to use
Decorative
Script

Colors
0094D4
00A9DD
6FCCEA
C7EBF8
E9F6FB
59FF00
82FF00
B8FF75
E3FFCB
F4FFEA
FFC000
F8CF3A
FAE287
FDF2CF
FEFAEE
F0912C
F2A743
F7CA91
FBE8D2
FDF5EE
EE7325
F08F49
F5BC92
FAE3D3
FDF4ED
EB3D1F
EC4F4E
F09395
F8D3D4
FCEDEE
E54698
E96AAD
F1A4CE
F9D9EA
FCEFF6

Requirements
Nice to have
• creativity

```html
<!DOCTYPE html>
<html lang="it">
<head>
<meta charset="utf-8">
<title>Luna Vita Chef – Biglietto da visita</title>
<link rel="stylesheet" href="https://fonts.googleapis.com/css2?family=Quicksand:wght@500;600&family=Roboto:wght@300;400&family=Alex+Brush&display=swap">
<style>
  :root {
    --bg: #2e2e2e;
    --sage: #8db8aa;
    --sage-deep: #7ba99a;
    --sage-soft: #a9cbbf;
    --paper: #f1f1f1;
    --paper-shade: #dcdcdc;
    --ink: #444444;
    --ink-soft: #555555;
    --band: #4a4a4a;
    --band-text: #e6e6e6;
  }
  * { box-sizing: border-box; margin: 0; padding: 0; }
  html, body {
    width: 1200px; height: 1138px; overflow: hidden;
    background: var(--bg);
  }
  .canvas { position: relative; width: 1200px; height: 1138px; }

  .card {
    position: absolute;
    width: 620px; height: 376px;
    border-radius: 16px;
    overflow: hidden;
  }

  /* Front */
  .card--front { left: 272px; top: 184px; background: var(--sage); }
  .card__photo-grid {
    position: absolute; inset: 0;
    background: linear-gradient(135deg, var(--sage-soft) 0%, var(--sage) 50%, var(--sage-deep) 100%);
  }
  .brand {
    position: absolute; left: 0; right: 0;
    text-align: center;
    font-family: "Quicksand", sans-serif;
    color: var(--ink);
  }
  .brand__name { font-weight: 600; font-size: 42px; letter-spacing: 0.5px; }
  .brand__tagline { font-weight: 500; font-size: 20px; }
  .brand__tagline sup { font-size: 12px; }
  .card--front .brand__name { top: 146px; }
  .card--front .brand__tagline { top: 206px; }

  .social {
    position: absolute;
    display: flex; align-items: center; gap: 10px;
    font-family: "Roboto", sans-serif; font-weight: 400;
    font-size: 17px; color: var(--ink-soft);
  }
  .social__dot {
    width: 16px; height: 16px; border-radius: 50%;
    background: var(--ink-soft);
  }
  .card--front .social { left: 0; right: 0; justify-content: center; top: 325px; }

  /* Back */
  .card--back {
    left: 274px; top: 606px;
    background: linear-gradient(180deg, var(--paper) 0%, #ebebeb 60%, var(--paper-shade) 100%);
  }
  .card--back .brand { left: 24px; right: auto; text-align: left; }
  .card--back .brand__name { top: 78px; }
  .card--back .brand__tagline { top: 138px; left: 72px; }

  .person {
    position: absolute; left: 24px; top: 238px;
    font-family: "Alex Brush", cursive; font-size: 32px;
    color: var(--ink);
  }
  .card--back .social { left: 24px; top: 305px; }

  .contacts {
    position: absolute; left: 358px; top: 236px;
    list-style: none;
    font-family: "Roboto", sans-serif; font-weight: 300;
    font-size: 16.5px; color: var(--ink);
  }
  .contacts li { display: flex; align-items: center; height: 24px; }
  .contacts svg { width: 15px; height: 15px; margin-right: 11px; fill: var(--sage-deep); stroke: var(--sage-deep); }

  .footer-strip {
    position: absolute; left: 0; bottom: 0;
    width: 330px; height: 14px;
    background: var(--sage);
  }
  .footer-band {
    position: absolute; left: 300px; bottom: 0;
    width: 320px; height: 46px;
    background: var(--band);
    clip-path: polygon(30px 0, 100% 0, 100% 100%, 0 100%);
    border-top-left-radius: 12px;
  }
  .vat {
    position: absolute; left: 360px; top: 339px;
    font-family: "Roboto", sans-serif; font-weight: 300;
    font-size: 16.5px; color: var(--band-text);
  }
</style>
</head>
<body>
<main class="canvas">

  <section class="card card--front" aria-label="Fronte del biglietto">
    <div class="card__photo-grid" role="img" aria-label="Griglia di foto di piatti sani, velata di verde salvia"></div>
    <div class="brand brand__name">Luna Vita Chef</div>
    <div class="brand brand__tagline">Leggerezza in ogni piatto<sup>®</sup></div>
    <div class="social"><span class="social__dot"></span>@Lunavita27</div>
  </section>

  <section class="card card--back" aria-label="Retro del biglietto">
    <div class="brand brand__name">Luna Vita Chef</div>
    <div class="brand brand__tagline">Leggerezza in ogni piatto<sup>®</sup></div>

    <div class="person">Livia Marchetti</div>
    <div class="social"><span class="social__dot"></span>@Lunavita27</div>

    <ul class="contacts">
      <li>
        <svg viewBox="0 0 16 16" aria-hidden="true"><path stroke="none" d="M2 5c0-2 3-3 6-3s6 1 6 3v1h-3V5H5v1H2zM4 7h8l2 6H2z"/></svg>
        000-0000-0000
      </li>
      <li>
        <svg viewBox="0 0 16 16" aria-hidden="true"><path stroke="none" d="M1 3h14v10H1z"/><path fill="none" stroke="#f1f1f1" stroke-width="1.2" d="M1 3l7 6 7-6M1 13l5-5M15 13l-5-5"/></svg>
        info@piattileggeriorto.it
      </li>
      <li>
        <svg viewBox="0 0 16 16" aria-hidden="true"><g fill="none" stroke-width="1.3"><circle cx="8" cy="8" r="6.5"/><ellipse cx="8" cy="8" rx="3" ry="6.5"/><path d="M1.5 8h13M2.5 5h11M2.5 11h11"/></g></svg>
        www.piattileggeriorto.it
      </li>
    </ul>

    <div class="footer-strip"></div>
    <div class="footer-band"></div>
    <div class="vat">Partita IVA 01234567890</div>
  </section>

</main>
</body>
</html>
```